Rice importer and exporter. We need a new design for a 18 kg plastic bag.

We want to create a new brand of rice. This type of rice is produced in southeast Asia, imported to Portugal and sold to the local market. The target are people 30+ years old of all ethnicity. The name of the brand should be 'Marevo', this is the name we want people to see and get used to it. <br/>Regarding the package itself. We want a simple bag, not with many different colours (3, 4 or 5) with preference to golden yellow. The Front page, should have our brand 'Marevo' and the exact description of the type of rice 'Arroz 100% Jasmin Perfumado' and 'Premium Quality'. In the bag should also be included the nutrition facts, cooking instructions, a trasnparent part where customer can see the quality of the product and the our company info. Finally we would like to see in the front page the five stars and on the back the triple AAA (see examples of attached files). All the remaining should be of your imagination. <br/>Finally, the image 3 is an example of a bag structure that we want to make.

Target Market(s)

People 30+ years old

Font styles to use
Serif
Sans Serif

Colors
ffc214
fec214
fee18a
fbee3f
faef58
fbf289

Requirements
Must have
• 5 Stars on the front page, triple A's on the back and a transparent area for the customers to see the quality of the rice.

```html
<!DOCTYPE html>
<html lang="pt">
<head>
<meta charset="utf-8">
<title>Marevo – Arroz 100% Jasmin Perfumado 18kg</title>
<link href="https://fonts.googleapis.com/css2?family=Oswald:wght@400;500;600&family=Montserrat:wght@900&family=Cinzel:wght@700&display=swap" rel="stylesheet">
<style>
  :root{
    --gold:#ffc214;
    --gold-soft:#fee18a;
    --lemon:#fbee3f;
    --cream:#fbf289;
    --orange:#f07a22;
    --orange-deep:#e8631a;
    --brown:#3a1608;
    --field-green:#8cbf3f;
    --bg:#f4f5f7;
  }
  html,body{margin:0;padding:0;width:1200px;height:943px;overflow:hidden;background:var(--bg);}
  .canvas{position:relative;width:1200px;height:943px;}
  .bag-front{
    position:absolute;left:312px;top:31px;width:575px;height:880px;overflow:hidden;
    background:radial-gradient(ellipse at 50% 62%, #fffbe0 0%, var(--cream) 22%, var(--lemon) 45%, var(--gold) 85%);
    font-family:'Oswald',sans-serif;
  }
  .brand-band{
    position:absolute;left:159px;top:0;width:255px;height:300px;
    background:linear-gradient(180deg,var(--orange-deep) 0%,var(--orange) 40%,#f8a62a 100%);
  }
  .brand-plate{position:absolute;left:154px;top:270px;width:265px;height:155px;}
  .brand-company{
    position:absolute;left:0;right:0;top:276px;text-align:center;
    font-family:'Cinzel',serif;font-size:10px;color:#8a1a10;letter-spacing:1px;
  }
  .brand-name{
    position:absolute;left:0;right:0;top:293px;text-align:center;
    font-family:'Montserrat',sans-serif;font-weight:900;font-size:49px;line-height:1;color:var(--brown);letter-spacing:1px;
  }
  .dots{position:absolute;left:175px;width:225px;border-top:3px dotted var(--brown);}
  .dots.top{top:290px}.dots.bottom{top:354px}
  .stars{position:absolute;left:0;right:0;top:360px;display:flex;justify-content:center;gap:4px;}
  .product-title{
    position:absolute;left:0;right:0;text-align:center;color:var(--orange);
    font-weight:500;font-size:42px;line-height:1;letter-spacing:.5px;
  }
  .product-title.line1{top:456px}
  .product-title.line2{top:513px}
  .landscape{
    position:absolute;left:0;top:590px;width:575px;height:290px;
    background:linear-gradient(180deg,#a8d6c4 0%,#7fbf5a 18%,#9ccc3e 40%,#e6e43a 65%,var(--lemon) 100%);
  }
  .rice-window{position:absolute;left:55px;top:574px;width:215px;height:245px;}
  .info-panel{
    position:absolute;left:244px;top:685px;width:266px;height:138px;
    background:linear-gradient(180deg,#ffd060,#f9a531);
    border:2px solid #d4892a;border-radius:4px;box-shadow:0 2px 4px rgba(120,60,0,.35);
  }
  .quality-title{position:absolute;left:22px;top:8px;font-size:29px;font-weight:600;color:var(--brown);line-height:1;letter-spacing:.3px;}
  .panel-rule{position:absolute;left:22px;right:14px;border-top:2px dotted var(--brown);}
  .panel-rule.a{top:49px}.panel-rule.b{top:124px}
  .weight-label{position:absolute;left:22px;top:55px;font-size:18px;font-weight:500;color:var(--brown);line-height:1;}
  .weight-value{position:absolute;left:20px;top:75px;font-size:44px;font-weight:600;color:var(--brown);line-height:1;}
  .importer{
    position:absolute;left:130px;top:56px;width:130px;border-left:1px dotted var(--brown);padding-left:5px;
    font-size:6.5px;line-height:1.35;color:var(--brown);
  }
  .importer strong{font-weight:600;display:block;margin-bottom:6px;}
  .importer .gap{display:block;height:6px;}
  .quality-seal{position:absolute;left:156px;top:742px;width:88px;height:88px;}
</style>
</head>
<body>
<main class="canvas">
  <section class="bag-front" aria-label="Frente do saco de arroz Marevo">
    <div class="brand-band"></div>
    <svg class="brand-plate" viewBox="0 0 265 155" aria-hidden="true">
      <path d="M0 8 H12 V0 H253 V8 H265 V100 H253 V108 H200 A68 68 0 0 1 65 108 H12 V100 H0 Z" fill="#f79a2a" stroke="#e0751a" stroke-width="2"/>
      <line x1="80" y1="130" x2="185" y2="130" stroke="#b8551a" stroke-width="1"/>
    </svg>
    <div class="brand-company">TAVO &amp; REIS LDA</div>
    <div class="dots top"></div>
    <div class="brand-name">MAREVO</div>
    <div class="dots bottom"></div>
    <div class="stars" aria-label="Cinco estrelas">
      <svg width="110" height="20" viewBox="0 0 110 20" aria-hidden="true">
        <g fill="#2b1006">
          <polygon id="st" points="10,1 12.6,7.3 19.5,7.6 14.1,11.9 16,18.6 10,14.8 4,18.6 5.9,11.9 0.5,7.6 7.4,7.3"/>
          <use href="#st" x="22"/><use href="#st" x="44"/><use href="#st" x="66"/><use href="#st" x="88"/>
        </g>
      </svg>
    </div>

    <div class="product-title line1">ARROZ 100%</div>
    <div class="product-title line2">JASMIN PERFUMADO</div>

    <div class="landscape" role="img" aria-label="Paisagem de campos de arroz verdes e amarelos com colinas ao fundo"></div>

    <svg class="rice-window" viewBox="0 0 215 245" role="img" aria-label="Janela transparente com grãos de arroz jasmim">
      <path d="M8 4 C120 40 200 110 200 200 C200 230 175 244 150 240 C60 220 5 130 8 4 Z" fill="#f3efe4" stroke="#f07a22" stroke-width="8"/>
      <path d="M90 20 C160 50 205 110 212 165" fill="none" stroke="#f07a22" stroke-width="10" stroke-linecap="round"/>
      <path d="M40 90 C70 150 110 200 160 232" fill="none" stroke="#f07a22" stroke-width="5" stroke-linecap="round"/>
    </svg>

    <div class="info-panel">
      <div class="quality-title">PREMIUM QUALITY</div>
      <div class="panel-rule a"></div>
      <div class="weight-label">PESO LIQUIDO:</div>
      <div class="weight-value">18KG</div>
      <div class="importer">
        <strong>IMPORTADO POR: TAVO &amp; REIS LDA</strong>
        RUA DAS OLIVEIRAS ARMAZÉM B4<br>2700-100 AMADORA PORTUGAL
        <span class="gap"></span>
        TELEFONE: 912345678<br>EMAIL: GERAL@TAVOREIS.PT<br>WEBSITE: WWW.TAVOREIS.PT
      </div>
      <div class="panel-rule b"></div>
    </div>

    <svg class="quality-seal" viewBox="0 0 88 88" aria-label="Selo 100% Premium Quality">
      <circle cx="44" cy="44" r="42" fill="#f4a21e"/>
      <circle cx="44" cy="44" r="35" fill="#d28a14"/>
      <circle cx="44" cy="44" r="31" fill="#4a0f0c"/>
      <g font-family="Cinzel, serif" font-weight="700" fill="#f6e3c0" text-anchor="middle">
        <text x="44" y="39" font-size="13">100%</text>
        <text x="44" y="52" font-size="10">PREMIUM</text>
        <text x="44" y="63" font-size="9">QUALITY</text>
      </g>
    </svg>
  </section>
</main>
</body>
</html>
```